Figure for presentation on a hybrid research project

We need a figure that shows a series of 6 technical projects feeding into 3 multidisciplinary hybrid projects.
The concept is a ring of 6 technical projects, which could look like a 6 colour swirl (see
https://en.plorvanex.org/wiki/Vector_graphics for an example of a 4 colour swirl.)
The 3 hybrid projects sit in the centre because they rely on input from many of the surrounding technical projects.
I've drawn a rough version in Powerpoint - see attached file uploaded. Note, in my example I couldn't draw the swirling outer ring and the colour selection is poor. The acronym for the overall Centre using the figure is VexORDA, so we will have a mint leaf and turquoise green in the logo, plus also nerves, since we will be researching neural interconnections.
We ABSOLUTELY NEED the final form of the figure to include vector graphics formats (including a form that can be edited in Photoshop) because we may need to change the title of the technical projects or of the hybrid projects at short notice ourselves.

Target Market(s)

Academic: eminent scientists and engineers

Industry/Entity Type

Technical

Font styles to use
Sans Serif

Colors
04a990

Requirements
Must have
• The projects around the ring with all project titles legible; the final figure will be reduced to no more than 8cm x 8cm in the proposal (probably less).
• Only one colour selected, because we have included that colour in the logo that we are having designed. Otherwise, a colour series around the ring that is pleasant, and another compatible colour series for the inter 3 projects.
• We ABSOLUTELY NEED the final form of the figure to include vector graphics formats (including a form that can be edited in Photoshop) because we may need to change the title of the technical projects or of the hybrid projects at short notice ourselves.
Nice to have
• See the figure we uploaded; that's the essence
• HOWEVER VIP: two of the titles around the outer ring have changed slightly.
• Computational Modelling is now Neuronal Modelling and
• Signal Processing is now Non-Invasive Interfaces (note that I've now changed the titles on the uploaded figure)

```html
<!DOCTYPE html>
<html lang="en">
<head>
<meta charset="utf-8">
<title>VexORDA Research Programme Structure</title>
<link rel="stylesheet" href="https://fonts.googleapis.com/css2?family=Montserrat:wght@700;800&display=swap">
<style>
  :root {
    --canvas-bg: #ffffff;
    --divider: #ffffff;
    --blade-living: #06735a;
    --blade-gene: #07a088;
    --blade-electro: #067a62;
    --blade-optrode: #08957c;
    --blade-neuronal: #056a53;
    --blade-noninvasive: #0a987e;
    --hub-action: #22bcee;
    --hub-action-deep: #1a9ad2;
    --hub-wiring: #0a98d0;
    --hub-wiring-deep: #0672a8;
    --hub-perception: #0a36b4;
    --hub-perception-deep: #05208a;
    --label: #ffffff;
  }
  html, body {
    margin: 0;
    padding: 0;
    width: 1200px;
    height: 999px;
    overflow: hidden;
    background: var(--canvas-bg);
  }
  .programme-figure {
    display: block;
    width: 1200px;
    height: 999px;
  }
  .blade {
    stroke: var(--divider);
    stroke-width: 5;
    stroke-linejoin: round;
  }
  .blade--living { fill: var(--blade-living); }
  .blade--gene { fill: var(--blade-gene); }
  .blade--electro { fill: var(--blade-electro); }
  .blade--optrode { fill: var(--blade-optrode); }
  .blade--neuronal { fill: var(--blade-neuronal); }
  .blade--noninvasive { fill: var(--blade-noninvasive); }
  .project-title {
    font-family: "Montserrat", sans-serif;
    font-weight: 700;
    font-size: 22px;
    fill: var(--label);
  }
  .hub-outline {
    fill: none;
    stroke: var(--divider);
    stroke-width: 5;
  }
  .hub-segment {
    stroke: var(--divider);
    stroke-width: 4;
  }
  .hub-title {
    font-family: "Montserrat", sans-serif;
    font-weight: 800;
    font-size: 34px;
    fill: var(--label);
    text-anchor: middle;
  }
</style>
</head>
<body>
<svg class="programme-figure" viewBox="0 0 1130 950" width="1200" height="999" xmlns="http://www.w3.org/2000/svg" role="img" aria-label="Six technical projects swirling around three hybrid projects">
  <defs>
    <radialGradient id="hub-action-fill" cx="0.45" cy="0.3" r="0.8">
      <stop offset="0" stop-color="var(--hub-action)"/>
      <stop offset="1" stop-color="var(--hub-action-deep)"/>
    </radialGradient>
    <radialGradient id="hub-wiring-fill" cx="0.5" cy="0.4" r="0.8">
      <stop offset="0" stop-color="var(--hub-wiring)"/>
      <stop offset="1" stop-color="var(--hub-wiring-deep)"/>
    </radialGradient>
    <radialGradient id="hub-perception-fill" cx="0.5" cy="0.7" r="0.7">
      <stop offset="0" stop-color="var(--hub-perception)"/>
      <stop offset="1" stop-color="var(--hub-perception-deep)"/>
    </radialGradient>
    <filter id="hub-shadow" x="-30%" y="-30%" width="160%" height="160%">
      <feDropShadow dx="0" dy="0" stdDeviation="14" flood-color="#00251c" flood-opacity="0.45"/>
    </filter>

    <path id="path-living" d="M225.9,432.9 A242,242 0 0 1 672.8,348.5"/>
    <path id="path-gene" d="M426.9,163.1 A242,242 0 0 1 723.4,507.9"/>
    <path id="path-noninvasive" d="M359.1,741.8 A242,242 0 0 1 509.4,312.5"/>
    <path id="path-electro" d="M610.8,647.5 A258,258 0 0 0 771.0,189.9"/>
    <path id="path-optrode" d="M433.4,603.7 A258,258 0 0 0 909.9,513.7"/>
    <path id="path-neuronal" d="M382.6,428.2 A258,258 0 0 0 698.8,795.8"/>
  </defs>

  <g class="technical-ring">
    <path class="blade blade--living" d="M220.86,472 A250,250 0 1 1 708.62,472 A250,250 0 0 0 220.86,472 Z"/>
    <path class="blade blade--gene" d="M390.43,178.30 A250,250 0 1 1 634.31,600.71 A250,250 0 0 0 390.43,178.30 Z"/>
    <path class="blade blade--electro" d="M729.57,178.30 A250,250 0 1 1 485.69,600.71 A250,250 0 0 0 729.57,178.30 Z"/>
    <path class="blade blade--optrode" d="M899.14,472 A250,250 0 1 1 411.38,472 A250,250 0 0 0 899.14,472 Z"/>
    <path class="blade blade--neuronal" d="M729.57,765.70 A250,250 0 1 1 485.69,343.29 A250,250 0 0 0 729.57,765.70 Z"/>
    <path class="blade blade--noninvasive" d="M390.43,765.70 A250,250 0 1 1 634.31,343.29 A250,250 0 0 0 390.43,765.70 Z"/>

    <text class="project-title"><textPath href="#path-living" startOffset="50%" text-anchor="middle">Living Electrodes</textPath></text>
    <text class="project-title"><textPath href="#path-gene" startOffset="50%" text-anchor="middle">Gene Regulated Interfaces</textPath></text>
    <text class="project-title"><textPath href="#path-electro" startOffset="50%" text-anchor="middle">Electro-modulated Interfaces</textPath></text>
    <text class="project-title"><textPath href="#path-optrode" startOffset="50%" text-anchor="middle">Optrode Interfaces</textPath></text>
    <text class="project-title"><textPath href="#path-neuronal" startOffset="50%" text-anchor="middle">Neuronal Modelling</textPath></text>
    <text class="project-title"><textPath href="#path-noninvasive" startOffset="50%" text-anchor="middle">Non-invasive Interfaces</textPath></text>
  </g>

  <g class="hybrid-hub">
    <circle cx="560" cy="472" r="190" fill="url(#hub-perception-fill)" filter="url(#hub-shadow)"/>
    <path class="hub-segment" fill="url(#hub-action-fill)"
          d="M560,472 C515,445 500,330 602.7,286.9 A190,190 0 0 0 379.3,530.7 C430,575 545,560 560,472 Z"/>
    <path class="hub-segment" fill="url(#hub-wiring-fill)"
          d="M560,472 C515,445 500,330 602.7,286.9 A190,190 0 0 1 709.7,589.0 C700,515 630,455 560,472 Z"/>
    <circle class="hub-outline" cx="560" cy="472" r="190"/>

    <text class="hub-title" x="453" y="474">ACTION</text>
    <text class="hub-title" x="637" y="394">BRAIN</text>
    <text class="hub-title" x="637" y="437">WIRING</text>
    <text class="hub-title" x="560" y="603">PERCEPTION</text>
  </g>
</svg>
</body>
</html>
```